Web Design for an Innovative Life Science Marketplace

IMPORTANT:
The software is called CS-Cart. It has capabilities and limitations with design features in the software. There is a certain framework that needs to be followed. It is PHP and Linux. It may require add-ons for your design, so please be specific with what is required. It’s preferred the designer has CS-Cart knowledge/experience.

Key Requirements
1. I’d like the design to include an implemented/recommended CS-Cart theme that is consistent with our branding (see the marketing collateral and logo).
2. I then need the additional design changes to that theme to create the below web pages.
3. All designs should be consistent with our branding. All pictures should either be computer generated (clip art-like) or pictures of happy patients. What is a happy patient? Close up photo of someone healthy, happy, and experiencing/enjoying life. Not someone in a hospital or getting care. Please see examples already on the site.

Please see the attached Web Design details in the word document. That document is important to complete the design.

```html
<!DOCTYPE html>
<html lang="en">
<head>
<meta charset="utf-8">
<title>CycleLink LS – Life Science Marketplace</title>
<link href="https://fonts.googleapis.com/css2?family=Gelasio:wght@400;500&family=Lato:wght@400;700&family=Poppins:wght@400;500;600&display=swap" rel="stylesheet">
<style>
:root{
  --green:#8dc03f;
  --green-dark:#7aaa30;
  --teal:#2d6a5b;
  --text:#555a5c;
  --text-dark:#3c4143;
  --grey-bg:#f4f4f4;
  --white:#ffffff;
  --line:#e3e3e3;
}
*{box-sizing:border-box;margin:0;padding:0}
html,body{width:1200px;height:2917px;overflow:hidden;background:var(--white)}
body{position:relative;font-family:"Lato",sans-serif;color:var(--text)}
.abs{position:absolute}
a{color:inherit;text-decoration:none}

/* top bar */
.topbar{position:absolute;left:0;top:0;width:1200px;height:43px;background:var(--green);color:var(--white);font-family:"Poppins",sans-serif;font-size:14px}
.topbar .item{position:absolute;top:11px;display:flex;align-items:center;gap:12px}

/* header */
.header{position:absolute;left:0;top:43px;width:1200px;height:103px;background:var(--white)}
.brand{position:absolute;left:78px;top:30px;display:flex;align-items:center;gap:12px;font-family:"Poppins",sans-serif;font-weight:600;font-size:25px;color:var(--green)}
.brand .dot{width:34px;height:34px;border-radius:50%;background:var(--green)}
.nav{position:absolute;right:78px;top:38px;display:flex;gap:32px;font-family:"Lato",sans-serif;font-size:15.5px;color:var(--text-dark)}
.nav .active{color:var(--teal);font-weight:700}

/* hero */
.hero{position:absolute;left:0;top:146px;width:1200px;height:580px;overflow:hidden}
.hero-photo{position:absolute;inset:0;background:linear-gradient(90deg,#e4e4e4 0%,#d6d4d2 35%,#e9d7c6 60%,#efe3d6 80%,#e3e1de 100%)}
.hero-curve{position:absolute;left:0;bottom:0}
.hero h1{position:absolute;left:78px;top:160px;font-family:"Gelasio",serif;font-weight:500;font-size:31px;color:var(--teal)}
.hero p{position:absolute;left:78px;top:216px;width:400px;font-size:17px;line-height:27px;color:var(--text-dark)}
.btn{display:inline-flex;align-items:center;justify-content:center;font-family:"Poppins",sans-serif;font-weight:600;font-size:17px;color:var(--white);background:var(--green);border-radius:4px;box-shadow:0 2px 4px rgba(0,0,0,.15)}
.btn.outline{background:var(--white);color:var(--green);border:2px solid var(--green);box-shadow:none;font-weight:500}
.hero .btn{position:absolute;left:78px;top:340px;width:186px;height:49px}
.scroll-down{position:absolute;left:580px;top:656px;width:40px;height:58px;border-radius:20px;background:var(--white);border:2px solid #dcdcdc;display:flex;align-items:center;justify-content:center}

/* headings */
.sec-title{position:absolute;left:0;width:1200px;text-align:center;font-family:"Gelasio",serif;font-weight:500;font-size:29px;color:var(--green)}
.sec-title span{color:var(--teal)}

/* welcome */
.welcome-text{position:absolute;left:260px;top:840px;width:680px;text-align:center;font-size:14.5px;line-height:27px}
.welcome-text p+p{margin-top:25px}
.welcome .btn{position:absolute;left:527px;top:1085px;width:146px;height:51px}

/* join */
.join{position:absolute;left:0;top:1197px;width:1200px;height:366px;background:var(--grey-bg)}
.role{position:absolute;top:128px;width:360px;text-align:center}
.role .icon{width:62px;height:62px;margin:0 auto;background:var(--green);border-radius:6px;transform:rotate(-8deg);display:flex;align-items:center;justify-content:center;box-shadow:0 2px 4px rgba(0,0,0,.2)}
.role .icon svg{transform:rotate(8deg)}
.role h3{margin-top:20px;font-family:"Poppins",sans-serif;font-weight:500;font-size:18px;color:var(--teal)}
.role p{margin-top:6px;font-size:14.5px;line-height:26px}

/* products */
.products h2{position:absolute;left:80px;top:1620px;font-family:"Gelasio",serif;font-weight:500;font-size:29px;color:var(--green)}
.products .intro{position:absolute;left:80px;top:1684px;width:345px;font-size:15px;line-height:27px}
.products .btn{position:absolute;left:78px;top:1875px;width:146px;height:51px}
.prod-grid{position:absolute;left:467px;top:1622px;width:645px;height:305px}
.prod-grid .vline{position:absolute;left:313px;top:0;width:1px;height:305px;background:var(--line)}
.prod-grid .hline{position:absolute;left:0;top:154px;width:645px;height:1px;background:var(--line)}
.prod{position:absolute;width:290px}
.prod h4{display:flex;align-items:center;gap:18px;font-family:"Poppins",sans-serif;font-weight:600;font-size:17.5px;color:var(--teal)}
.prod p{margin-top:10px;font-size:14.5px;line-height:26px}

/* marketing */
.marketing{position:absolute;left:0;top:1990px;width:1200px;height:322px;background:var(--grey-bg)}
.marketing-photo{position:absolute;left:0;top:0;width:486px;height:322px;background:linear-gradient(90deg,#3b2b25 0%,#8a6b5c 30%,#d8b7a2 55%,#e9e5e3 85%,#f4f4f4 100%)}
.marketing h2{position:absolute;left:548px;top:58px;font-family:"Gelasio",serif;font-weight:500;font-size:29px;color:var(--green)}
.marketing h2 span{color:var(--teal)}
.marketing p{position:absolute;left:548px;top:118px;width:480px;font-size:14.5px;line-height:26px}
.marketing .btn{position:absolute;top:208px;height:52px}

/* promise */
.promise-quote{position:absolute;left:0;top:2434px;width:1200px;text-align:center;font-family:"Poppins",sans-serif;font-weight:500;font-size:18px;line-height:29px;color:var(--text-dark)}

/* footer */
.footer{position:absolute;left:0;top:2548px;width:1200px;height:369px;color:var(--white)}
.footer svg.wave{position:absolute;left:0;top:0}
.foot-nav{position:absolute;left:0;top:106px;width:1200px;display:flex;justify-content:center;gap:22px;font-size:15px}
.foot-nav i{font-style:normal;opacity:.9}
.contact{position:absolute;top:158px;width:360px;text-align:center}
.contact h5{margin-top:10px;font-family:"Poppins",sans-serif;font-weight:600;font-size:16.5px}
.contact p{margin-top:6px;font-size:14.5px;line-height:25px}
.foot-rule{position:absolute;left:78px;top:307px;width:1044px;height:1px;background:rgba(255,255,255,.55)}
.copy{position:absolute;left:80px;top:328px;font-family:"Poppins",sans-serif;font-weight:500;font-size:14px}
.social{position:absolute;right:78px;top:322px;display:flex;gap:8px}
.social span{width:30px;height:30px;border:1.5px solid var(--teal);border-radius:2px;display:block}
.social span.filled{background:var(--teal)}
</style>
</head>
<body>

<div class="topbar">
  <div class="item" style="left:78px">
    <svg width="16" height="16" viewBox="0 0 24 24"><path fill="#2d6a5b" d="M6.6 10.8a15 15 0 0 0 6.6 6.6l2.2-2.2c.3-.3.7-.4 1-.2 1.1.4 2.3.6 3.6.6.6 0 1 .4 1 1V20c0 .6-.4 1-1 1A17 17 0 0 1 3 4c0-.6.4-1 1-1h3.5c.6 0 1 .4 1 1 0 1.3.2 2.5.6 3.6.1.3 0 .7-.2 1z"/></svg>
    <span>+1 844-555-0172</span>
  </div>
  <div class="item" style="left:336px">
    <svg width="17" height="13" viewBox="0 0 24 18"><path fill="#2d6a5b" d="M0 0h24v18H0z"/><path fill="none" stroke="#8dc03f" stroke-width="2" d="M1 1l11 9 11-9"/></svg>
    <span>hello@cyclelinkls.com</span>
  </div>
  <div class="item" style="left:988px">
    <svg width="17" height="17" viewBox="0 0 24 24"><circle cx="12" cy="7" r="5" fill="#2d6a5b"/><path fill="#2d6a5b" d="M2 23c0-6 4-9 10-9s10 3 10 9z"/></svg>
    <span>Login</span>
  </div>
  <div class="item" style="left:1086px;top:10px">
    <svg width="24" height="22" viewBox="0 0 24 22"><path fill="none" stroke="#2d6a5b" stroke-width="2" d="M1 7h22l-3 11H4z M7 7l4-6 M17 7l-4-6"/></svg>
  </div>
</div>

<header class="header">
  <div class="brand"><span class="dot"></span>CycleLink LS</div>
  <nav class="nav">
    <a class="active">Home</a><a>About Us</a><a>Why CycleLink LS?</a><a>Our Partners</a><a>White Paper</a><a>Quality Policy</a>
  </nav>
</header>

<section class="hero">
  <div class="hero-photo" role="img" aria-label="Photo of a smiling mother hugging her young daughter in a bright room"></div>
  <svg class="hero-curve" width="1200" height="130" viewBox="0 0 1200 130" preserveAspectRatio="none"><path fill="#ffffff" d="M0 130 L0 118 C60 100 140 98 260 96 L1080 96 C1150 96 1180 70 1200 40 L1200 130 Z"/></svg>
  <h1>Join the Circular Supply Chain</h1>
  <p>“A virtual multi-vendor marketplace and for the life sciences community to connect and transact before and after-market materials and equipment”</p>
  <a class="btn">Pre-Register Now!</a>
</section>
<div class="scroll-down">
  <svg width="16" height="20" viewBox="0 0 16 20"><path fill="none" stroke="#2d6a5b" stroke-width="2.4" d="M8 1v16 M2 11l6 6 6-6"/></svg>
</div>

<section class="welcome">
  <h2 class="sec-title" style="top:776px">Welcome To <span>CycleLink LS</span></h2>
  <div class="welcome-text">
    <p>Lorem Ipsum is simply dummy text of the printing and typesetting industry. Lorem Ipsum has been the industry's standard dummy text ever since the 1500s, when an unknown printer took a galley of type and scrambled it to make a type specimen book. It has survived not only five centuries, but also the leap into electronic typesetting, remaining essentially unchanged.</p>
    <p>It was popularised in the 1960s with the release of Typeface sheets containing Lorem Ipsum passages, and more recently with desktop publishing software like Quillset Publisher including versions of Lorem Ipsum.</p>
  </div>
  <a class="btn">Read More</a>
</section>

<section class="join">
  <h2 class="sec-title" style="top:58px">Who Shold <span>Join?</span></h2>
  <div class="role" style="left:59px">
    <div class="icon"><svg width="34" height="30" viewBox="0 0 34 30"><path fill="#2d6a5b" d="M2 28V14l8 5v-5l8 5v-5l8 5V2h5v26z"/></svg></div>
    <h3>Manufacturers</h3>
    <p>Create an Account in Minutes to Sell/Buy<br>Excess or Obsolete Materials and Equipment.</p>
  </div>
  <div class="role" style="left:420px">
    <div class="icon"><svg width="32" height="32" viewBox="0 0 32 32"><circle cx="16" cy="16" r="13" fill="none" stroke="#2d6a5b" stroke-width="2.5"/><circle cx="12" cy="13" r="3" fill="#2d6a5b"/><circle cx="20" cy="13" r="3" fill="#2d6a5b"/><path fill="#2d6a5b" d="M7 23c1-4 9-4 9 0zM16 23c1-4 9-4 9 0z"/></svg></div>
    <h3>Researchers</h3>
    <p>Sell/Buy Low-Cost Materials and Receive<br>Donations.</p>
  </div>
  <div class="role" style="left:781px">
    <div class="icon"><svg width="32" height="32" viewBox="0 0 32 32"><circle cx="10" cy="6" r="4" fill="#2d6a5b"/><circle cx="22" cy="6" r="4" fill="#2d6a5b"/><path fill="#2d6a5b" d="M5 12h10v10h-2v8H7v-8H5zM17 12h10v10h-2v8h-6v-8h-2z"/></svg></div>
    <h3>Original Suppliers</h3>
    <p>Market Your Products Across a Broad Life<br>Sciences Network.</p>
  </div>
</section>

<section class="products">
  <h2>Products</h2>
  <p class="intro">Lorem Ipsum is simply dummy text of the printing and typesetting industry. Lorem Ipsum has been the industry's standard dummy text ever since the 1500s, when an unknown printer took a galley of type and scrambled it to make a type specimen book.</p>
  <a class="btn">Read More</a>
  <div class="prod-grid">
    <div class="vline"></div><div class="hline"></div>
    <div class="prod" style="left:20px;top:0">
      <h4><svg width="30" height="34" viewBox="0 0 30 34"><rect x="2" y="2" width="26" height="30" rx="3" fill="#2d6a5b"/><rect x="6" y="11" width="18" height="9" fill="#8dc03f"/></svg>Raw Materials</h4>
      <p>Consumable and starting materials for API and intermediate manufacturing or research.</p>
    </div>
    <div class="prod" style="left:333px;top:0">
      <h4><svg width="36" height="34" viewBox="0 0 36 34"><circle cx="12" cy="21" r="9" fill="none" stroke="#2d6a5b" stroke-width="5" stroke-dasharray="4 3"/><circle cx="26" cy="9" r="6" fill="none" stroke="#8dc03f" stroke-width="4" stroke-dasharray="3 2"/></svg>Equipment</h4>
      <p>End item systems manufactured for LS applications</p>
    </div>
    <div class="prod" style="left:20px;top:178px">
      <h4><svg width="32" height="32" viewBox="0 0 32 32"><circle cx="16" cy="16" r="14" fill="#2d6a5b"/><circle cx="16" cy="16" r="8" fill="#8dc03f"/><circle cx="16" cy="16" r="3" fill="#2d6a5b"/></svg>Parts</h4>
      <p>Components of a modular system used for LS applications</p>
    </div>
    <div class="prod" style="left:333px;top:178px">
      <h4><svg width="34" height="32" viewBox="0 0 34 32"><circle cx="8" cy="6" r="4" fill="#2d6a5b"/><circle cx="26" cy="26" r="4" fill="#2d6a5b"/><path fill="#8dc03f" d="M18 3h10v8l-3-3-4 4-2-2 4-4zM16 29H6v-8l3 3 4-4 2 2-4 4z"/></svg>Collaborative Relationships</h4>
      <p>Safety Stock Agreements, Advertising/Selling/ Donating Capacity, joint supplier audits, etc.</p>
    </div>
  </div>
</section>

<section class="marketing">
  <div class="marketing-photo" role="img" aria-label="Close-up photo of a smiling young woman with dark hair"></div>
  <h2>Marketing <span>Materials</span></h2>
  <p>Lorem Ipsum is simply dummy text of the printing and typesetting industry. Lorem Ipsum has dummy text ever since the 1500s,</p>
  <a class="btn" style="left:547px;width:237px">Read Our White Paper</a>
  <a class="btn outline" style="left:796px;width:208px">Read Our Brochure</a>
</section>

<section class="promise">
  <h2 class="sec-title" style="top:2368px"><span>Our</span> Promise</h2>
  <p class="promise-quote">“A greener, more cost-efficient, and quality-driven supply chain<br>through a collaborative life sciences marketplace”</p>
</section>

<footer class="footer">
  <svg class="wave" width="1200" height="369" viewBox="0 0 1200 369" preserveAspectRatio="none"><path fill="#8dc03f" d="M0 369V110C20 80 60 68 140 66L1060 14C1130 10 1170 20 1200 36V369Z"/></svg>
  <nav class="foot-nav">
    <a>Home</a><i>|</i><a>About Us</a><i>|</i><a>Why CycleLink LS?</a><i>|</i><a>Our Partners</a><i>|</i><a>White Papers</a><i>|</i><a>Quality Policy</a>
  </nav>
  <div class="contact" style="left:59px">
    <svg width="18" height="18" viewBox="0 0 24 24"><path fill="#2d6a5b" d="M6.6 10.8a15 15 0 0 0 6.6 6.6l2.2-2.2c.3-.3.7-.4 1-.2 1.1.4 2.3.6 3.6.6.6 0 1 .4 1 1V20c0 .6-.4 1-1 1A17 17 0 0 1 3 4c0-.6.4-1 1-1h3.5c.6 0 1 .4 1 1 0 1.3.2 2.5.6 3.6.1.3 0 .7-.2 1z"/></svg>
    <h5>Phone</h5>
    <p>+1 844-555-0172</p>
  </div>
  <div class="contact" style="left:420px">
    <svg width="16" height="20" viewBox="0 0 16 22"><path fill="#2d6a5b" d="M8 0a8 8 0 0 1 8 8c0 6-8 14-8 14S0 14 0 8a8 8 0 0 1 8-8z"/><circle cx="8" cy="8" r="3" fill="#8dc03f"/></svg>
    <h5>Address</h5>
    <p>Unit 4A 12 Harbour Lane<br>Westvale NSW 2150</p>
  </div>
  <div class="contact" style="left:781px">
    <svg width="18" height="14" viewBox="0 0 24 18"><path fill="#2d6a5b" d="M0 0h24v18H0z"/><path fill="none" stroke="#8dc03f" stroke-width="2" d="M1 1l11 9 11-9"/></svg>
    <h5>E-mail</h5>
    <p>hello@cyclelinkls.com</p>
  </div>
  <div class="foot-rule"></div>
  <p class="copy">© CYCLELINK LS - 2018. All Rights Reserved.</p>
  <div class="social"><span class="filled"></span><span></span><span></span><span></span></div>
</footer>

</body>
</html>
```